Wine Bottle Label for Tall Fern Wines

We are a small, newly established winery in need of an original, bold and outstanding bottle label design for our Tall Fern wine.

Our vineyard and winery are located on a 200 acre farm in a remote part of southern Oregon. The name "Tall Fern" was inspired by the large, overgrown size of all of the foliage here, including our grapevines. Things grow large and vigorous in Oregon! And everything is very lush and green. It is almost surreal or other-worldly, like the landscapes seen in the Keeper of The Stones movies, or the land of Quill. It is a place that makes you say "wow" with its epic, large scale, natural beauty.

The name "Tall Fern" also captures the essence of our wine. It is big in flavor, quality and color. Our first release is a Pinot Noir (red). Pinot Noir wines often are subtle in flavor and thin in their color. Our label should convey that our Pinot Noir is a much more robust, darker, heavier, meatier, more flavorful wine that is a lot more fun than an "ordinary" wine. At the same time, this wine is not cheap, and so nothing in the label should convey "bargain," "low price," or "cheapness." This is a fine wine with a sense of adventure. Be sure to convey "quality" with your design along with "big," "adventure" and "fun".

The label should appeal to a younger demographic, both male and female, between the ages of 21 and 35. It should be non-traditional and adventurous and suggest a pushing of boundaries and a breaking of rules. This Pinot Noir does not conform to the normal "limitations" of the variety, therefore the label should not conform. It should have an "organic" or "natural" or "agricultural" vibe, as opposed to something mechanical or technical. It should, however, be contemporary. Do not confuse "natural" or "organic" with being nostalgic or old school. Think "agri-hipsters."

The label should be designed to fit on a Burgundy-style wine bottle (photo attached for reference). (Note: All Pinot Noir and Chardonnay is bottled in Burgundy bottles, If you are not sure about the bottle shape you can go to a local store and compare the various bottles. Locate a bottle of Pinot Noir or Chardonnay or anything identified as a "Burgundy Wine," and it should be the correct bottle. The tall, skinny bottles used for Cabernet Sauvignon are NOT correct)). Please see the "Must Have" notes for more on the bottle.

In summary, the final project should be a wine bottle label design that conveys bigness, vastness, adventurous, non-traditional, high quality wine. A good tagline to keep in mind is "Living Large."

Target Market(s)

Young, hip, non-conformist wine drinkers aged 21-35 with a sense of adventure and an appreciation of quality.

Industry/Entity Type

School

Requirements
Must have
• *Must contain the words:

Tall Fern (the brand)
2013 Pinot Noir (the vintage year and variety)

*The label must be designed to fit a Burgundy-style wine bottle. A photo is attached for reference.

*Additionally, the label needs to fit on the lower, widest part of the bottle. The label will be printed on sticky paper and rolled onto the bottle with a machine. The machine cannot apply labels to the neck of the bottle. The maximum size of a label that will fit this space is 5.5 inches wide by 4.5 inches tall. You DO NOT have to fill ALL of this space or confine the label shape to a rectangle, but the label cannot exceed this size or it won't stick to the bottle properly. It will really help if you can put your hands on an actual bottle to see the logistics of applying the label. But if that is not possible, just do your best with the instructions you have. I am confident the winning design could be adjusted to fit the bottle, if necessary
Nice to have
• *Wine grape leaf or leaves.

*A concept I have been playing with is sunlight shining through leaves like light through a Marlowe lamp or a stained glass window. This is NOT a requirement for this label. However, if the concept inspires and idea, I would be most happy to see it.
Should not have
• IF a leaf or leaves are included in the design (not a requirement) they MUST be wine grapevine leafs and preferably leaves of the Pinot Noir vine. Do not use generic leaves or identifiable leaves such as oak leaves, maple leaves, or anything that looks like the Canadian flag or the Halden Ridge Ravens hockey logo. Reference the attached photos of wine grape leaves to see the correct leaf type. I am happy to email more photos upon request. These photos may be used in whole or in part in your design, however, a leaf from a photo is NOT a requirement, nor is the image of a leaf or leaves.

This label should NOT be designed for Bordeaux-style wine bottles (the tall, skinny ones).

```html
<!DOCTYPE html>
<html lang="en">
<head>
<meta charset="utf-8">
<title>Tall Fern Pinot Noir 2013 – Bottle Label</title>
<link rel="stylesheet" href="https://fonts.googleapis.com/css2?family=Montserrat:wght@200;300&display=swap">
<style>
  :root {
    --page-bg: #ffffff;
    --stone-light: #c9c1b2;
    --stone-mid: #aea593;
    --stone-dark: #8c8474;
    --leaf-deep: #8e0d14;
    --leaf-red: #c8121b;
    --leaf-bright: #ee2a2a;
    --type-white: #ffffff;
    --type-red: #d8141c;
  }

  html, body {
    margin: 0;
    padding: 0;
    width: 1200px;
    height: 960px;
    overflow: hidden;
    background: var(--page-bg);
  }

  .label {
    position: absolute;
    left: 110px;
    top: 32px;
    width: 980px;
    height: 896px;
    overflow: hidden;
    background:
      radial-gradient(ellipse at 30% 70%, rgba(255,255,255,0.18), transparent 55%),
      linear-gradient(160deg, var(--stone-light) 0%, var(--stone-mid) 55%, var(--stone-dark) 100%);
    font-family: "Montserrat", "Helvetica Neue", Arial, sans-serif;
  }

  .label__vine-leaf {
    position: absolute;
    left: 272px;
    top: 26px;
    width: 690px;
    height: 856px;
    border-radius: 46% 40% 44% 52% / 38% 42% 50% 46%;
    background:
      linear-gradient(180deg, transparent 32%, rgba(60,0,0,0.35) 40%, transparent 48%),
      radial-gradient(ellipse at 55% 38%, var(--leaf-bright) 0%, var(--leaf-red) 40%, var(--leaf-deep) 100%);
  }

  .label__brand,
  .label__variety,
  .label__vintage {
    position: absolute;
    margin: 0;
    line-height: 1;
    text-transform: uppercase;
    white-space: nowrap;
  }

  .label__brand {
    font-weight: 200;
    color: var(--type-white);
    font-size: 230px;
    letter-spacing: 4px;
  }

  .label__brand--first { left: 40px; top: 28px; }
  .label__brand--second { left: 200px; top: 225px; }

  .label__variety {
    left: 42px;
    top: 470px;
    font-weight: 200;
    font-size: 118px;
    letter-spacing: 1px;
    color: var(--type-white);
  }

  .label__vintage {
    left: 626px;
    top: 594px;
    font-weight: 300;
    font-size: 84px;
    letter-spacing: 2px;
    color: var(--type-red);
  }
</style>
</head>
<body>
  <main class="label">
    <div class="label__vine-leaf" role="img" aria-label="Large red grapevine leaf containing a vineyard landscape under glowing red light"></div>
    <h1 class="label__brand label__brand--first">Tall</h1>
    <p class="label__brand label__brand--second">Fern</p>
    <p class="label__variety">Pinot Noir</p>
    <p class="label__vintage">2013</p>
  </main>
</body>
</html>
```